Website Re-design and extension of an existing website

I have a Wordpress website currently and I need it to be upgraded. I have MOST of the content to get it started and the rest (video's, pictures ect) are on the way. I want to know if it is possible to convert my existing website into a Personal Brand website with a public speaking emphasis. I would like to have my website modeled after the following website:

http://www.vokalmira.com/

I have attached a document entitled "Website Outline & Content" that has all of the text on it and it has red headlines that indicate where something needs to be added or designed. I will be happy to give more detail if needed.

Things I still need to get to you in order to design the website;

-Demo video
-Full length public speaking video

Target Market(s)

Corporations, universities, trade associations, private events

Coding

Coded - Design and coding required

Requirements
Must have
• Pictures, links, downloadable forms, MULTIPLE video's embedded, my logo, keep the colors in sync with my existing marketing material
Nice to have
• I would like my design colors thematic as already inherent in my marketing materials (see my Speaker One Sheet)

```html
<!DOCTYPE html>
<html lang="en">
<head>
<meta charset="utf-8">
<title>Brent Calloway – Your Holistic Lifestyle Hacker</title>
<link href="https://fonts.googleapis.com/css2?family=Roboto:wght@300;400;500;700&family=Roboto+Condensed:wght@700&display=swap" rel="stylesheet">
<style>
:root{
  --olive:#6f7240;
  --olive-dark:#5c5f33;
  --olive-deep:#4d5030;
  --olive-light:#8d8f5c;
  --ink:#333333;
  --muted:#777777;
  --grey-bg:#efefef;
  --footer:#262626;
  --footer-low:#1d1d1d;
  --white:#ffffff;
}
*{margin:0;padding:0;box-sizing:border-box}
html,body{width:1200px;height:4433px;overflow:hidden}
body{font-family:"Roboto",Arial,sans-serif;color:var(--ink);background:var(--white);position:relative}
.abs{position:absolute}
section,header,footer{position:absolute;left:0;width:1200px;overflow:hidden}

/* header */
.site-header{top:0;height:88px;background:var(--white)}
.brand{left:133px;top:20px;display:flex;align-items:center;gap:10px}
.brand-dot{width:44px;height:44px;border-radius:50%;background:var(--olive)}
.brand-name{font-family:"Roboto Condensed",sans-serif;font-weight:700;font-size:28px;color:var(--olive);line-height:1}
.brand-tag{font-size:9px;letter-spacing:1px;color:var(--muted);text-transform:uppercase;margin-top:2px}
.follow{right:133px;top:32px;display:flex;align-items:center;gap:8px;font-size:11px;font-weight:700;color:var(--ink)}
.follow span.c{width:24px;height:24px;border-radius:50%;background:var(--olive)}
.main-nav{top:88px;height:24px;background:var(--olive-dark);display:flex;padding-left:126px}
.main-nav a{color:var(--white);font-size:10px;font-weight:700;text-transform:uppercase;text-decoration:none;padding:0 11px;line-height:24px;white-space:nowrap}
.main-nav a.active{background:var(--olive-light)}

/* hero */
.hero{top:112px;height:500px;background:linear-gradient(180deg,#9db4c9 0%,#c7b79a 45%,#6c6a55 75%,#3c3a2e 100%)}
.hero-panel{left:133px;top:88px;width:355px;height:230px;background:rgba(111,114,64,.82);padding:22px 40px;color:var(--white)}
.hero-panel h1{font-size:28px;font-weight:700;margin-bottom:12px}
.hero-panel li{list-style:none;font-size:19px;font-weight:300;margin-bottom:14px}
.hero-panel li::before{content:"›";margin-right:10px}
.hero-btn{left:133px;top:325px;width:355px;height:71px;background:var(--olive-dark);border:2px solid rgba(255,255,255,.7);color:var(--white);font-size:16px;font-weight:700;text-transform:uppercase;text-align:center;padding-top:12px;line-height:1.3}
.dots{left:548px;top:435px;display:flex;gap:9px}
.dots i{width:10px;height:10px;border-radius:50%;border:1.5px solid var(--white)}
.dots i.on{background:var(--white)}

/* intro */
.intro{top:612px;height:482px;background:var(--white)}
.book{left:266px;top:56px;width:242px;height:361px;background:linear-gradient(180deg,#f3ecd6 0%,#e7dcbb 55%,#cf9a42 100%);box-shadow:3px 4px 10px rgba(0,0,0,.3)}
.intro-mark{left:591px;top:70px;width:50px;height:50px;border-radius:50%;background:var(--olive)}
.intro h2{left:591px;top:142px;font-size:24px;font-weight:700;color:var(--olive)}
.intro .sub{left:591px;top:175px;font-size:17px;color:var(--ink)}
.dl-btn{left:591px;width:331px;height:41px;border:2px solid var(--olive);font-size:14px;line-height:37px;text-align:center;color:var(--ink)}

/* sugar */
.sugar{top:1094px;height:502px;background:var(--olive)}
.sugar-photo{left:532px;top:0;width:668px;height:502px;background:linear-gradient(90deg,var(--olive) 0%,#6a5d3c 30%,#3b3427 70%,#2e2a22 100%)}
.sugar h2{left:139px;top:52px;font-size:22px;font-weight:700;color:var(--white);line-height:1.3}
.ill{left:139px;display:flex;align-items:center;gap:28px;color:var(--white);font-size:18px;font-weight:300}
.ill .ico{width:52px;height:52px;border-radius:50%;border:2px solid rgba(255,255,255,.8);display:flex;align-items:center;justify-content:center}

/* about */
.about{top:1596px;height:497px;background:var(--olive-deep)}
.about-photo{left:0;top:0;width:576px;height:497px;background:linear-gradient(135deg,#8fa07a 0%,#6f7a55 50%,#d9c2a3 100%)}
.about-mark{left:1030px;top:10px;width:230px;height:230px;border-radius:50%;background:rgba(255,255,255,.06)}
.about .kicker{left:640px;top:78px;font-size:20px;color:var(--white);font-weight:300}
.about h2{left:640px;top:102px;font-size:26px;font-weight:700;color:var(--white)}
.about p{left:640px;top:170px;width:480px;font-size:12.5px;line-height:1.75;color:#e6e6d8;font-weight:300}

/* testimonials */
.testimonials{top:2093px;height:443px;background:var(--grey-bg)}
.section-title{width:1200px;text-align:center;font-size:24px;font-weight:700;color:var(--ink)}
.rule{left:575px;width:50px;height:3px;background:var(--olive)}
.card{top:147px;width:290px;height:237px;background:var(--white);padding:34px 28px 0 52px;font-size:12.5px;line-height:1.55;color:var(--muted)}
.card .q{position:absolute;font-size:60px;color:#cfcfcf;font-family:Georgia,serif;line-height:1}
.card .who{position:absolute;left:52px;bottom:26px;display:flex;align-items:center;gap:12px;font-size:10px;font-weight:700;text-transform:uppercase;color:var(--ink)}
.card .who i{width:32px;height:32px;border-radius:50%;background:#b9a58d}
.arrow{top:235px;font-size:40px;color:#888;font-weight:300}

/* video */
.video{top:2536px;height:450px;background:var(--white)}
.video h2{left:133px;top:88px;font-size:24px;font-weight:700}
.video .rule2{left:133px;top:126px;width:44px;height:3px;background:var(--olive)}
.video p{left:133px;top:150px;width:330px;font-size:13px;line-height:1.6;color:var(--muted)}
.btn-olive{background:var(--olive-dark);color:var(--white);font-size:12px;font-weight:700;text-transform:uppercase;text-align:center}
.video-frame{left:526px;top:53px;width:538px;height:337px;background:linear-gradient(180deg,#a9b4bd 0%,#8d8e80 45%,#55564a 100%)}
.play{left:760px;top:185px;width:70px;height:70px;border-radius:50%;background:rgba(255,255,255,.85)}

/* articles */
.articles{top:2986px;height:502px;background:var(--grey-bg)}
.post{top:138px;width:292px}
.post .img{height:166px}
.post h3{font-size:13px;font-weight:700;margin:22px 0 8px;line-height:1.35;color:var(--ink)}
.post p{font-size:12px;line-height:1.5;color:var(--muted);width:260px}
.post .more{width:90px;height:24px;line-height:24px;margin-top:18px;font-size:10px}

/* clients */
.clients{top:3488px;height:266px;background:var(--white)}
.client{top:142px;width:162px;height:65px;border:1px solid #dcdcdc;display:flex;align-items:center;justify-content:center;gap:8px;font-size:17px;font-weight:500;color:#555}
.client i{width:12px;height:12px;background:#555}

/* cta */
.cta{top:3754px;height:272px;background:linear-gradient(90deg,#3f4127 0%,#5a5c3a 50%,#3b3d26 100%)}
.cta p{width:1200px;top:92px;text-align:center;color:var(--white);font-size:27px;font-weight:400;line-height:1.4}

/* footer */
.site-footer{top:4026px;height:407px;background:var(--footer)}
.f-head{top:42px;font-size:12px;font-weight:700;color:#b8ba85;text-transform:uppercase}
.f-menu{left:130px;top:76px;list-style:none;font-size:12px;line-height:1.7;color:#ccc}
.f-contact{left:372px;top:76px;font-size:12px;line-height:1.55;color:#ccc}
.f-contact div{display:flex;gap:14px;margin-bottom:16px}
.f-contact svg{flex:none;margin-top:2px}
.field{height:30px;background:#555;color:#bbb;font-size:11px;padding:7px 10px}
.submit{left:656px;top:230px;width:92px;height:26px;line-height:26px;background:#a8a86a;color:var(--white);font-size:11px;font-weight:700;text-align:center;text-transform:uppercase}
.f-bottom{top:320px;left:0;width:1200px;height:87px;background:var(--footer-low)}
.copy{right:133px;top:40px;font-size:11px;color:#aaa}
</style>
</head>
<body>

<header class="site-header">
  <div class="abs brand">
    <span class="brand-dot"></span>
    <div><div class="brand-name">BRENT CALLOWAY</div><div class="brand-tag">Your Holistic Lifestyle Hacker</div></div>
  </div>
  <div class="abs follow">FOLLOW US <span class="c"></span><span class="c"></span><span class="c"></span><span class="c"></span></div>
</header>
<nav class="abs main-nav" style="position:absolute;left:0;width:1200px">
  <a class="active">Home</a><a>About Brent Calloway</a><a>Motivational Speaker/Keynote</a><a>Workshop Presenter</a><a>Author</a><a>Coaching</a><a>Blog</a><a>Online Courses</a><a>Contact Brent Calloway</a>
</nav>

<section class="hero" role="img" aria-label="Speaker standing on a wooden bridge at sunset with mountains behind">
  <div class="abs hero-panel">
    <h1>BRENT CALLOWAY</h1>
    <ul><li>Sugar Addiction Expert</li><li>Holistic Health Expert</li><li>Author &amp; Speaker</li></ul>
  </div>
  <div class="abs hero-btn">See how Brent Calloway can help<br>you or your organization</div>
  <div class="abs dots"><i class="on"></i><i></i><i></i><i></i><i></i></div>
</section>

<section class="intro">
  <svg class="abs" style="left:0;top:0" width="1200" height="482"><polygon points="0,482 0,0 600,0 80,482" fill="#f2f2f2"/></svg>
  <div class="abs book" role="img" aria-label="Book cover: man with head in hands, yellow title cloud"></div>
  <div class="abs intro-mark"></div>
  <h2 class="abs">Your Holistic Lifestyle Hacker</h2>
  <div class="abs sub">Lose Your Mind &amp; Find Your Health!</div>
  <div class="abs dl-btn" style="top:230px">Download Brent's Speaker One Sheet</div>
  <div class="abs dl-btn" style="top:292px">Download Brent's Media Sheet</div>
  <div class="abs dl-btn" style="top:355px">Download Brent's College Speaker One Sheet</div>
</section>

<section class="sugar">
  <div class="abs sugar-photo" role="img" aria-label="Speaker in sunglasses at sunset by a lake"></div>
  <h2 class="abs">Sugar Addiction<br>(The Stealth Addiction) is destroying</h2>
  <div class="abs ill" style="top:142px"><span class="ico"><svg width="22" height="22"><rect x="4" y="2" width="14" height="18" fill="none" stroke="#fff" stroke-width="2"/><line x1="7" y1="8" x2="15" y2="8" stroke="#fff" stroke-width="2"/></svg></span>Your bottom-line</div>
  <div class="abs ill" style="top:213px"><span class="ico"><svg width="24" height="24"><path d="M2 12 A10 10 0 0 1 22 12 Z" fill="#fff"/><line x1="12" y1="12" x2="12" y2="21" stroke="#fff" stroke-width="2"/></svg></span>Your Insurance Premiums</div>
  <div class="abs ill" style="top:293px"><span class="ico"><svg width="24" height="24"><circle cx="12" cy="10" r="6" fill="none" stroke="#fff" stroke-width="2"/><rect x="9" y="17" width="6" height="4" fill="#fff"/></svg></span>The health of your employees</div>
  <div class="abs ill" style="top:373px"><span class="ico"><svg width="24" height="24"><circle cx="12" cy="12" r="9" fill="none" stroke="#fff" stroke-width="2"/><circle cx="12" cy="12" r="3" fill="#fff"/></svg></span>The culture of your company</div>
</section>

<section class="about">
  <div class="abs about-photo" role="img" aria-label="Portrait of the speaker smiling outdoors"></div>
  <div class="abs about-mark"></div>
  <div class="abs kicker">About</div>
  <h2 class="abs">Brent Calloway</h2>
  <p class="abs">For over 17 years, Brent Calloway has tirelessly helped executives, employees, and everyday people achieve lasting health and fitness by helping them "lose their minds." Using his Whole-Self Method, speaking platform, and online training courses, Brent has helped hundreds of people shed their limiting beliefs, eat better, beat sugar addiction and transform their bodies and minds. Brent delights in helping people see through the self-deception of being "normal," and he invites his students to discover and accept the extraordinary people they truly are. If you are ready to transform physically, mentally, emotionally, and spiritually, it is time for you to meet Brent Calloway, your Holistic Health Hacker!</p>
</section>

<section class="testimonials">
  <div class="abs section-title" style="top:45px">Testimonials</div>
  <div class="abs rule" style="top:90px"></div>
  <div class="abs arrow" style="left:70px">‹</div>
  <div class="abs arrow" style="left:1100px">›</div>
  <div class="abs card" style="left:139px"><span class="q" style="left:18px;top:20px">“</span>There are many variations of passages of Lorem Ipsum available, but the majority have suffered alteration in some form, by injected humour, or randomised words which don't look even slightly believable.<span class="q" style="right:20px;top:150px">”</span><div class="who"><i></i>Colin Ferris</div></div>
  <div class="abs card" style="left:456px"><span class="q" style="left:18px;top:20px">“</span>There are many variations of passages of Lorem Ipsum available, but the majority have suffered alteration in some form, by injected humour, or randomised words which don't look even slightly believable.<span class="q" style="right:20px;top:150px">”</span><div class="who"><i></i>Simon Hale</div></div>
  <div class="abs card" style="left:774px"><span class="q" style="left:18px;top:20px">“</span>There are many variations of passages of Lorem Ipsum available, but the majority have suffered alteration in some form, by injected humour, or randomised words which don't look even slightly believable.<span class="q" style="right:20px;top:150px">”</span><div class="who"><i></i>Owen Marsh</div></div>
</section>

<section class="video">
  <h2 class="abs">Our Video</h2>
  <div class="abs rule2"></div>
  <p class="abs">It is a long established fact that a reader will be distracted by the readable content of a page when looking at its layout. The point of using Lorem Ipsum is that it has a more-or-less normal distribution of letters, as opposed to using 'Content here, content here', making it look like readable English. Many desktop publishing packages and web page editors</p>
  <div class="abs btn-olive" style="left:133px;top:330px;width:122px;height:32px;line-height:32px">Watch Video</div>
  <div class="abs video-frame" role="img" aria-label="Video still of the speaker outdoors with mountains"></div>
  <div class="abs play"><svg width="70" height="70"><polygon points="28,20 28,50 52,35" fill="#777"/></svg></div>
</section>

<section class="articles">
  <div class="abs section-title" style="top:45px">Latest Articles</div>
  <div class="abs rule" style="top:90px"></div>
  <div class="abs post" style="left:136px"><div class="img" role="img" aria-label="Man pushing a red lawn mower on grass" style="background:linear-gradient(180deg,#6a8a3a,#b53a2a 60%,#4f6e2c)"></div><h3>Why You Continue To Eat Junk Food Despite Your "Will Power"</h3><p>There are many variations of passages of Lorem Ipsum available, but the</p><div class="more btn-olive">Read More</div></div>
  <div class="abs post" style="left:455px"><div class="img" role="img" aria-label="Smooth grey pebbles with a heart-shaped stone" style="background:linear-gradient(135deg,#7c7670,#c9c3bb 50%,#6d665f)"></div><h3>Do I Really LOVE Myself?</h3><p>There are many variations of passages of Lorem Ipsum available, but the</p><div class="more btn-olive">Read More</div></div>
  <div class="abs post" style="left:774px"><div class="img" role="img" aria-label="Small child in a pink shirt" style="background:linear-gradient(135deg,#e6d9c6,#d7a3a8 60%,#c9b59a)"></div><h3>"But I DESERVE It!" Why Self-Entitlement Drives Overeating &amp; Disease</h3><p>There are many variations of passages of Lorem Ipsum available, but the</p><div class="more btn-olive">Read More</div></div>
</section>

<section class="clients">
  <div class="abs section-title" style="top:36px">Our Clients</div>
  <div class="abs rule" style="top:80px"></div>
  <div class="abs client" style="left:148px"><i></i>Harlow</div>
  <div class="abs client" style="left:331px">Brightmart</div>
  <div class="abs client" style="left:519px">Wellgrove</div>
  <div class="abs client" style="left:707px">T&amp;K</div>
  <div class="abs client" style="left:895px">Ridgeway</div>
</section>

<section class="cta" role="img" aria-label="Dark olive-toned photo of the speaker">
  <p class="abs">Become a Holistic Health Hacker and receive<br>a FREE 30-Day Meal Plan crafted by Brent!</p>
</section>

<footer class="site-footer">
  <div class="abs f-head" style="left:130px">Menu</div>
  <ul class="f-menu abs"><li>Home</li><li>About Brent Calloway</li><li>Motivational Speaker/Keynote</li><li>Workshop Presenter</li><li>Author, Coaching</li><li>Blog</li><li>Online Courses</li><li>Contact Brent Calloway</li></ul>
  <div class="abs f-head" style="left:372px">Contact Us</div>
  <div class="abs f-contact">
    <div><svg width="12" height="16"><path d="M6 0a6 6 0 0 1 6 6c0 4-6 10-6 10S0 10 0 6a6 6 0 0 1 6-6z" fill="#b8ba85"/><circle cx="6" cy="6" r="2" fill="#262626"/></svg><span>2240 Cedar Bluff Lane<br>Millbrook, PA 17900</span></div>
    <div><svg width="12" height="14"><rect x="1" y="0" width="10" height="14" rx="2" fill="#b8ba85"/></svg><span>800-555-0142</span></div>
    <div><svg width="14" height="10"><rect width="14" height="10" fill="#b8ba85"/><polyline points="0,0 7,6 14,0" fill="none" stroke="#262626"/></svg><span>hello@brentcalloway.com</span></div>
  </div>
  <div class="abs f-head" style="left:656px">Contact Us</div>
  <div class="abs field" style="left:656px;top:76px;width:200px">Name</div>
  <div class="abs field" style="left:866px;top:76px;width:200px">E-mail</div>
  <div class="abs field" style="left:656px;top:124px;width:410px;height:90px">Message</div>
  <div class="abs submit">Submit</div>
  <div class="abs f-bottom">
    <div class="abs brand" style="top:20px">
      <span class="brand-dot" style="background:#9a9c64"></span>
      <div><div class="brand-name" style="color:#b8ba85">BRENT CALLOWAY</div><div class="brand-tag" style="color:#888">Your Holistic Lifestyle Hacker</div></div>
    </div>
    <div class="abs copy">Copyrights @ 2017 All Rights Reserved</div>
  </div>
</footer>

</body>
</html>
```